KESTREL Academy Exhibit Booth Posters

My company is KESTREL Academy (a division of KESTREL for Growth). We are exhibiting in a month, and I need to re-do my exhibit booth posters. There will be a total of 4 posters needed. Sizes are below.
1) Top- 11 feet long X 12 inches wide (Try to match color scheme in example photo)
2) Center- 4 feet long X 2 feet wide (Chalkboard background)
3) Left- 18 inches long X 2 feet wide (Cork-board back ground with the use of push pins holding up post-it-notes, paper, etc.)
4) Right- 18 inches long X 2 feet wide (Cork-board back ground with the use of push pins holding up post-it-notes, paper, etc.)
I have attached a photo of my old booth. This will get you an idea of the size, color schemes, and more. I have created basic rendering of each poster. The content is important, but the look and design should be drastically improved.
The websites to look into for ideas are:
www.kestrelforgrowth.example
www.kestrelacademy.example
Updates
I've added a new file. It's a .JPG of the certification diploma. Thanks!
Target Market(s)
Business Owners, Managers, HR, Supervisors, Teens who want to boost their resume
Industry/Entity Type
It Company
Look and feel

```html
<!DOCTYPE html>
<html lang="en">
<head>
<meta charset="utf-8">
<title>KESTREL Academy – Success @ Work Poster</title>
<link href="https://fonts.googleapis.com/css2?family=Arimo:ital,wght@0,400;0,700;1,700&family=Roboto+Condensed:wght@700&family=UnifrakturMaguntia&family=Pinyon+Script&display=swap" rel="stylesheet">
<style>
  :root{
    --page:#ffffff;
    --wood:#b8844a;
    --wood-dark:#8a5a2b;
    --wood-light:#d6a86c;
    --cork:#c79a68;
    --cork-dark:#a8784a;
    --headline-red:#e3262a;
    --paper-warm-1:#fbe7c9;
    --paper-warm-2:#f6c99a;
    --paper-white:#f7f8f8;
    --note-yellow:#fbf28c;
    --note-shadow:rgba(60,35,10,.35);
    --label-green:#1b7a2b;
    --gold:#b8912e;
    --ink:#2a2a2a;
    --photo-1:#7f8a94;
    --photo-2:#c9cfd4;
    --banner-green:#b6d957;
    --banner-yellow:#f4f3b0;
  }
  *{box-sizing:border-box;margin:0;padding:0}
  html,body{width:1004px;height:1200px;overflow:hidden;background:var(--page)}
  .poster{position:relative;width:1004px;height:1200px}

  .board-frame{
    position:absolute;left:70px;top:29px;width:867px;height:1156px;
    background:linear-gradient(135deg,var(--wood-light),var(--wood) 40%,var(--wood-dark));
    padding:14px;box-shadow:0 2px 6px rgba(0,0,0,.35);
  }
  .cork{
    width:100%;height:100%;
    background:radial-gradient(ellipse at 50% 45%,var(--cork),var(--cork-dark));
    box-shadow:inset 0 0 8px rgba(0,0,0,.45);
  }

  .headline-paper{
    position:absolute;left:161px;top:107px;width:696px;height:214px;
    background:linear-gradient(120deg,var(--paper-warm-1),var(--paper-warm-2));
    box-shadow:3px 5px 8px var(--note-shadow);
    display:flex;align-items:center;justify-content:center;text-align:center;
  }
  .headline{
    font-family:"Arimo",Arial,sans-serif;font-weight:700;font-style:italic;
    font-size:43px;line-height:1.45;color:var(--headline-red);
  }

  .tape{position:absolute;width:52px;height:34px;background:rgba(245,245,240,.8);
    box-shadow:0 1px 2px rgba(0,0,0,.2)}
  .tape--left{left:190px;top:104px;transform:rotate(-30deg)}
  .tape--bottom{left:418px;top:300px;transform:rotate(8deg)}
  .tape--right{left:740px;top:102px;transform:rotate(35deg)}

  .certificate{
    position:absolute;left:148px;top:442px;width:464px;height:352px;
    background:var(--paper-white);transform:rotate(4deg);
    box-shadow:4px 6px 10px var(--note-shadow);padding:22px;
  }
  .certificate__border{
    width:100%;height:100%;border:6px double var(--gold);
    outline:2px solid var(--gold);outline-offset:-14px;
    display:flex;flex-direction:column;align-items:center;padding:20px 28px 0;
    text-align:center;color:var(--ink);position:relative;
  }
  .certificate__school{font-family:"UnifrakturMaguntia",serif;font-size:15px}
  .certificate__title{font-family:"UnifrakturMaguntia",serif;font-size:19px;margin-top:2px}
  .certificate__name{font-family:"Pinyon Script",cursive;font-size:18px;margin-top:4px;
    border-bottom:1px solid var(--ink);padding:0 30px}
  .certificate__small{font-family:"Arimo",Arial,sans-serif;font-size:5.5px;line-height:1.4;margin-top:6px}
  .certificate__course{font-family:"UnifrakturMaguntia",serif;font-size:16px;margin-top:3px}
  .certificate__footer{position:absolute;left:28px;right:28px;bottom:22px;display:flex;
    justify-content:space-between;align-items:flex-end;font-family:"Arimo",Arial,sans-serif;font-size:6px}
  .certificate__sign{border-top:1px solid var(--ink);width:110px;padding-top:2px;text-align:left}
  .certificate__seal{position:absolute;left:50%;bottom:48px;width:26px;height:26px;margin-left:-13px;
    border-radius:50%;background:radial-gradient(circle,#f5d66a,var(--gold))}

  .note{position:absolute;background:var(--note-yellow);box-shadow:3px 5px 8px var(--note-shadow)}
  .note--before{left:600px;top:361px;width:268px;height:255px;transform:rotate(2deg)}
  .note--after{left:613px;top:640px;width:257px;height:257px;transform:rotate(-1deg)}
  .note__label{position:absolute;left:0;right:0;text-align:center;
    font-family:"Arimo",Arial,sans-serif;font-weight:700;font-size:22px;color:var(--label-green)}
  .note--before .note__label{top:42px}
  .note--after .note__label{top:46px}
  .note__photo{position:absolute;border:2px solid #fff;
    background:linear-gradient(180deg,var(--photo-2),var(--photo-1))}
  .note--before .note__photo{left:18px;top:70px;width:230px;height:168px}
  .note--after .note__photo{left:18px;top:74px;width:220px;height:162px}

  .price-paper{
    position:absolute;left:134px;top:921px;width:709px;height:177px;
    background:linear-gradient(170deg,#fff 10%,var(--banner-yellow) 55%,var(--banner-green) 80%,#fff 96%);
    box-shadow:3px 5px 8px var(--note-shadow);
    display:flex;align-items:center;justify-content:center;text-align:center;
  }
  .price{font-family:"Roboto Condensed","Arial Narrow",sans-serif;font-weight:700;
    font-size:62px;line-height:1.3;color:var(--headline-red)}

  .pin{position:absolute;width:40px;height:44px}
</style>
</head>
<body>
<main class="poster">
  <div class="board-frame"><div class="cork"></div></div>

  <section class="headline-paper">
    <h1 class="headline">Get Your Employees<br>Certified in Success @ Work</h1>
  </section>
  <span class="tape tape--left"></span>
  <span class="tape tape--bottom"></span>

  <article class="certificate">
    <div class="certificate__border">
      <p class="certificate__school">Kestrel Academy</p>
      <p class="certificate__title">Graduation Certification</p>
      <p class="certificate__name">Jordan Avery Sample</p>
      <p class="certificate__small">This document certifies that the student named above has completed the course listed below with full honors and all the rights of a graduate.</p>
      <p class="certificate__course">Success At Work</p>
      <p class="certificate__small">Awarded by the faculty on the recommendation of the teaching staff as a record of strong performance.</p>
      <span class="certificate__seal" role="img" aria-label="Certificate seal"></span>
      <div class="certificate__footer">
        <span class="certificate__sign">Kestrel Academy Professor</span>
        <span class="certificate__sign">Date of Graduation</span>
      </div>
    </div>
  </article>

  <div class="note note--before">
    <div class="note__photo" role="img" aria-label="Photo of an employee before the course, wearing sunglasses and a dark polo shirt"></div>
    <span class="note__label">Before</span>
  </div>
  <div class="note note--after">
    <div class="note__photo" role="img" aria-label="Photo of the same employee after the course, smiling in a dark polo shirt with a name badge"></div>
    <span class="note__label">After</span>
  </div>

  <section class="price-paper">
    <p class="price">At a Price You<br>Cannot Pass Up!</p>
  </section>

  <svg class="pin" style="left:757px;top:78px" viewBox="0 0 40 44" aria-hidden="true">
    <defs><radialGradient id="pinBlue" cx="35%" cy="35%"><stop offset="0" stop-color="#8fc3ff"/><stop offset="1" stop-color="#1646a8"/></radialGradient></defs>
    <line x1="20" y1="22" x2="28" y2="42" stroke="#999" stroke-width="2"/>
    <circle cx="20" cy="18" r="15" fill="url(#pinBlue)"/>
  </svg>
  <svg class="pin" style="left:187px;top:460px" viewBox="0 0 40 44" aria-hidden="true">
    <defs><radialGradient id="pinRed" cx="35%" cy="35%"><stop offset="0" stop-color="#ff8a8a"/><stop offset="1" stop-color="#b00012"/></radialGradient></defs>
    <line x1="20" y1="22" x2="14" y2="42" stroke="#999" stroke-width="2"/>
    <circle cx="20" cy="18" r="15" fill="url(#pinRed)"/>
  </svg>
  <svg class="pin" style="left:500px;top:386px" viewBox="0 0 40 44" aria-hidden="true">
    <line x1="20" y1="22" x2="14" y2="42" stroke="#999" stroke-width="2"/>
    <circle cx="20" cy="18" r="15" fill="url(#pinRed)"/>
  </svg>
  <svg class="pin" style="left:754px;top:360px" viewBox="0 0 40 44" aria-hidden="true">
    <defs><radialGradient id="pinBlack" cx="35%" cy="35%"><stop offset="0" stop-color="#9a9a9a"/><stop offset="1" stop-color="#111"/></radialGradient></defs>
    <circle cx="20" cy="18" r="14" fill="url(#pinBlack)"/>
  </svg>
  <svg class="pin" style="left:750px;top:646px" viewBox="0 0 40 44" aria-hidden="true">
    <circle cx="20" cy="18" r="14" fill="url(#pinBlack)"/>
  </svg>
</main>
</body>
</html>
```